QZSTREAMHUB ( Wordpress website for catalogue of Vorlo Stream Pages)

Need a website to showcase different Vorlo Stream pages ( in different categories). Similar to e-commerce except no check-out / purchase of items. Pls use our logos provided and color scheme to be white+red+ blue as per our logo.

Target Market(s)

Consumers

Font styles to use
Sans Serif

Colors
ffffff
ec1f27
3276b5

Requirements
Must have
• I will need a Wordpress Theme as a handover. Also, pls use the color scheme (red+blue+white) as per logo attached. Prefer clean and near design with white space.

```html
<!DOCTYPE html>
<html lang="en">
<head>
<meta charset="utf-8">
<title>QZSTREAMHUB – A Portal of Curated Vorlo Stream</title>
<link href="https://fonts.googleapis.com/css2?family=Lato:wght@400;700;900&family=Oswald:wght@600;700&family=Roboto+Condensed:wght@700&display=swap" rel="stylesheet">
<style>
:root{
  --red:#e3101c;
  --blue:#2a5ab0;
  --footer-blue:#1c4fd2;
  --ink:#222;
  --text:#333;
  --grey-bg:#efefef;
  --hero-bg:#f1f1f1;
  --white:#fff;
}
*{box-sizing:border-box;margin:0;padding:0}
html,body{width:1200px;height:2856px;overflow:hidden}
body{position:relative;background:var(--white);font-family:"Lato",sans-serif;color:var(--text)}
.abs{position:absolute}
.heading{font-family:"Roboto Condensed",sans-serif;font-weight:700;color:var(--blue);text-transform:uppercase;text-align:center;font-size:29px;letter-spacing:.3px}
.btn{position:absolute;display:flex;align-items:center;justify-content:center;background:var(--red);color:var(--white);border-radius:24px;font-size:16px}
.btn.condensed{font-family:"Roboto Condensed",sans-serif;font-weight:700;font-size:17px;text-transform:uppercase}

/* header */
.brand{left:75px;top:40px;font-family:"Lato",sans-serif;font-weight:900;font-size:34px;color:var(--red);letter-spacing:-.5px}
.search{left:875px;top:28px;width:251px;height:33px;border:1px solid #ccc;border-radius:17px;font-size:14px;color:#444;padding:8px 20px}
.search svg{position:absolute;right:14px;top:9px}
.nav{top:86px;font-size:15.5px;font-weight:700;color:#222;text-transform:uppercase}
.nav.active{color:var(--red)}
.nav-underline{left:481px;top:111px;width:74px;height:3px;background:var(--red)}

/* hero */
.hero{left:0;top:124px;width:1200px;height:581px;background:radial-gradient(ellipse at 60% 50%,#fafafa,var(--hero-bg))}
.hero-title{left:55px;top:300px;font-family:"Oswald",sans-serif;font-weight:700;font-size:76px;line-height:64px;color:#141414;text-transform:uppercase}
.hero-title .of{font-family:"Lato",sans-serif;font-weight:900;font-size:54px;color:var(--red);text-transform:none}
.hero-title .badge{display:inline-block;background:var(--red);color:var(--white);padding:2px 8px 0;line-height:60px;margin-top:6px;border-radius:3px}
.hero-art{left:383px;top:238px;width:798px;height:344px;border-radius:30px;background:linear-gradient(120deg,#e4e8f5 0%,#c9d6f6 40%,#f3c9c9 75%,#d7e0fb 100%)}
.stripe{left:0;top:705px;width:1200px;height:13px;background:linear-gradient(100deg,var(--red) 0 46%,var(--footer-blue) 46% 100%)}

/* welcome */
.welcome-title{left:0;top:770px;width:1200px}
.welcome-text{left:89px;top:820px;width:1026px;text-align:center;font-size:15.5px;line-height:26.5px;color:#333}

/* categories */
.cat-bg{left:0;top:1029px;width:1200px;height:521px;background:var(--grey-bg)}
.cat-sub{left:0;top:1138px;width:1200px;text-align:center;font-size:15.5px}
.cat-card{top:1191px;width:331px;height:195px;background:var(--white)}
.cat-photo{position:absolute;left:47px;top:8px;width:237px;height:178px}
.cat-label{top:1414px;width:331px;text-align:center;font-family:"Roboto Condensed",sans-serif;font-weight:700;font-size:17px;color:var(--blue)}
.cat-desc{top:1443px;width:331px;text-align:center;font-size:14.5px}
.arrow{position:absolute}

/* featured */
.feat-card{top:1708px;width:326px;height:357px;border:1px solid #d6d6d6;background:var(--white)}
.feat-photo{position:absolute;left:42px;top:13px;width:241px;height:186px}
.feat-title{position:absolute;left:0;top:211px;width:100%;text-align:center;font-size:20px;color:var(--blue)}
.feat-desc{position:absolute;left:0;top:247px;width:100%;text-align:center;font-size:15px}
.feat-card .btn{left:72px;top:286px;width:180px;height:44px}

/* blog */
.blog-bg{left:0;top:2127px;width:1200px;height:479px;background:#f6f6f6}
.blog-photo{top:2252px;width:331px;height:189px}
.blog-title{top:2469px;width:331px;text-align:center;font-family:"Roboto Condensed",sans-serif;font-weight:700;font-size:17px;color:var(--red);text-transform:uppercase}
.blog-text{top:2497px;width:331px;text-align:center;font-size:15.5px;line-height:24px}

/* footer */
.footer{left:0;top:2606px;width:1200px;height:250px;background:var(--footer-blue);color:var(--white)}
.f-brand{left:75px;top:2671px;font-weight:900;font-size:36px;color:var(--white);letter-spacing:-.5px}
.f-small{font-size:12.5px;color:#e8eeff}
.f-head{font-family:"Roboto Condensed",sans-serif;font-weight:700;font-size:16px;color:var(--white);text-transform:uppercase}
.f-link{font-size:13px;color:#e8eeff}
.social{top:2786px;width:18px;height:18px;border-radius:50%;background:var(--white)}
.email-box{left:884px;top:2700px;width:242px;height:37px;background:var(--white);border-radius:19px;font-size:12px;color:#333;padding:11px 0 0 51px}
.email-box svg{position:absolute;left:18px;top:13px}
</style>
</head>
<body>

<!-- header -->
<div class="abs brand">QZSTREAMHUB</div>
<div class="abs search">Search..
  <svg width="14" height="14" viewBox="0 0 14 14"><circle cx="6" cy="6" r="4.3" fill="none" stroke="#111" stroke-width="2"/><line x1="9.2" y1="9.2" x2="13" y2="13" stroke="#111" stroke-width="2"/></svg>
</div>
<div class="abs nav active" style="left:497px">Home</div>
<div class="abs nav" style="left:597px">About Us</div>
<div class="abs nav" style="left:714px">Services</div>
<div class="abs nav" style="left:826px">Products</div>
<div class="abs nav" style="left:950px">Blog</div>
<div class="abs nav" style="left:1032px">Contact Us</div>
<div class="abs nav-underline"></div>

<!-- hero -->
<section class="abs hero"></section>
<div class="abs hero-art" role="img" aria-label="Illustration of a phone showing a live stream of dresses beside two cartoon shoppers with parcels, bags and a clothing rack"></div>
<h1 class="abs hero-title">A Portal <span class="of">of</span><br>Curated<br>Vorlo<br><span class="badge">Stream</span></h1>
<div class="abs stripe"></div>

<!-- welcome -->
<h2 class="abs heading welcome-title">Welcome to our website</h2>
<p class="abs welcome-text">Aliquam molestie, mi et imperdiet euismod, dui purus auctor tellus, et interdum lacus lectus et ante. Sed accumsan sollicitudin sapien, sit amet adipiscing turpis gravida ac. In congue, neque ac lobortis volutpat, libero mauris varius mi, vitae suscipit ipsum ligula vitae risus. Duis aliquam nibh a dui iaculis viverra id a velit. Vivamus egestas risus in magna varius commodo etiam pretium porttitor lectus..</p>
<a class="btn" style="left:511px;top:920px;width:180px;height:45px">READ MORE</a>

<!-- categories -->
<section class="abs cat-bg"></section>
<h2 class="abs heading" style="left:0;top:1085px;width:1200px">Categories</h2>
<p class="abs cat-sub">Aliquam molestie, mi et imperdiet euismod, dui purus auctor tellus, et interdum lacus lectus et ante.</p>

<svg class="arrow" style="left:38px;top:1294px" width="22" height="44" viewBox="0 0 22 44"><polyline points="20,2 2,22 20,42" fill="none" stroke="#888" stroke-width="2"/></svg>
<svg class="arrow" style="left:1140px;top:1294px" width="22" height="44" viewBox="0 0 22 44"><polyline points="2,2 20,22 2,42" fill="none" stroke="#888" stroke-width="2"/></svg>

<div class="abs cat-card" style="left:74px"><div class="cat-photo" role="img" aria-label="Photo of a room stacked with boxed electronics" style="background:linear-gradient(160deg,#6b5d52,#c9c3bb 55%,#3d3a38)"></div></div>
<div class="abs cat-card" style="left:434px"><div class="cat-photo" role="img" aria-label="Grid of photos of plush hair bands" style="background:linear-gradient(135deg,#f1dfe3,#9ccbe9 40%,#5a4136 75%,#eadcd7)"></div></div>
<div class="abs cat-card" style="left:795px"><div class="cat-photo" role="img" aria-label="Grid of photos of models wearing dresses" style="background:linear-gradient(135deg,#b9a7a8,#4f6673 40%,#c9c5cc 70%,#8f9aa3)"></div></div>

<div class="abs cat-label" style="left:74px">Dolorem ipsum</div>
<div class="abs cat-label" style="left:434px">Dolorem ipsum</div>
<div class="abs cat-label" style="left:795px">Dolorem ipsum</div>
<div class="abs cat-desc" style="left:74px">Maecenas in sem sed elit vulputate</div>
<div class="abs cat-desc" style="left:434px">Maecenas in sem sed elit vulputate</div>
<div class="abs cat-desc" style="left:795px">Maecenas in sem sed elit vulputate</div>

<a class="btn condensed" style="left:480px;top:1529px;width:239px;height:44px">View all categories</a>

<!-- featured -->
<h2 class="abs heading" style="left:0;top:1641px;width:1200px">Featured Vorlo Stream Pages</h2>

<svg class="arrow" style="left:38px;top:1864px" width="22" height="44" viewBox="0 0 22 44"><polyline points="20,2 2,22 20,42" fill="none" stroke="#888" stroke-width="2"/></svg>
<svg class="arrow" style="left:1140px;top:1864px" width="22" height="44" viewBox="0 0 22 44"><polyline points="2,2 20,22 2,42" fill="none" stroke="#888" stroke-width="2"/></svg>

<div class="abs feat-card" style="left:74px">
  <div class="feat-photo" role="img" aria-label="Grid of food menu promotion images" style="background:linear-gradient(135deg,#d9c9b6,#9a3f2a 40%,#4a4a4a 70%,#58a13b)"></div>
  <div class="feat-title">Duis in auctor sapien</div>
  <div class="feat-desc">Maecenas in sem sed elit vulputate</div>
  <a class="btn condensed">Read more</a>
</div>
<div class="abs feat-card" style="left:439px">
  <div class="feat-photo" role="img" aria-label="Grid of fresh fruit photos" style="background:linear-gradient(135deg,#c9b23a,#c0271e 35%,#3f3a33 65%,#c45b2c)"></div>
  <div class="feat-title">Duis in auctor sapien</div>
  <div class="feat-desc">Maecenas in sem sed elit vulputate</div>
  <a class="btn condensed">Read more</a>
</div>
<div class="abs feat-card" style="left:802px">
  <div class="feat-photo" role="img" aria-label="Grid of photos of plush hair bands" style="background:linear-gradient(135deg,#f1dfe3,#9ccbe9 40%,#5a4136 75%,#eadcd7)"></div>
  <div class="feat-title">Duis in auctor sapien</div>
  <div class="feat-desc">Maecenas in sem sed elit vulputate</div>
  <a class="btn condensed">Read more</a>
</div>

<!-- blog -->
<section class="abs blog-bg"></section>
<h2 class="abs heading" style="left:0;top:2190px;width:1200px">Blog Posts</h2>
<div class="abs blog-photo" style="left:74px;background:linear-gradient(135deg,#8a7d6c,#2c3a52 50%,#c9b79f)" role="img" aria-label="Photo of hands typing on a laptop showing a social sign-up page"></div>
<div class="abs blog-photo" style="left:436px;background:linear-gradient(135deg,#2f3b6a,#c9c9cf 45%,#3a2f2e 75%,#b88c3a)" role="img" aria-label="Photo of a shop shelf with kitchen appliances"></div>
<div class="abs blog-photo" style="left:796px;background:linear-gradient(135deg,#e8d45a,#c9a08a 40%,#9fb3d1 70%,#e7e3d6)" role="img" aria-label="Photo of hands holding a phone with social notification bubbles"></div>
<div class="abs blog-title" style="left:74px">Duis aliquam nibh a dui</div>
<div class="abs blog-title" style="left:436px">Duis aliquam nibh a dui</div>
<div class="abs blog-title" style="left:796px">Duis aliquam nibh a dui</div>
<p class="abs blog-text" style="left:74px">Aliquam molestie, mi et imperdiet euismod, dui purus auctor tellus et.</p>
<p class="abs blog-text" style="left:436px">Aliquam molestie, mi et imperdiet euismod, dui purus auctor tellus et.</p>
<p class="abs blog-text" style="left:796px">Aliquam molestie, mi et imperdiet euismod, dui purus auctor tellus et.</p>

<!-- footer -->
<footer class="abs footer"></footer>
<div class="abs f-brand">QZSTREAMHUB</div>
<div class="abs f-small" style="left:75px;top:2728px;line-height:20px">Copyright © 2020. Company Name.<br>All Right Reserved</div>
<div class="abs social" style="left:73px" aria-label="Social link"></div>
<div class="abs social" style="left:108px" aria-label="Social link"></div>
<div class="abs social" style="left:146px" aria-label="Social link"></div>
<div class="abs social" style="left:183px" aria-label="Social link"></div>
<div class="abs social" style="left:221px" aria-label="Social link"></div>

<div class="abs f-head" style="left:347px;top:2664px">Quick Links</div>
<div class="abs f-link" style="left:347px;top:2692px">Home</div>
<div class="abs f-link" style="left:347px;top:2719px">About us</div>
<div class="abs f-link" style="left:347px;top:2746px">Services</div>
<div class="abs f-link" style="left:447px;top:2692px">Products</div>
<div class="abs f-link" style="left:447px;top:2719px">Blog</div>
<div class="abs f-link" style="left:447px;top:2746px">Contact us</div>

<div class="abs f-head" style="left:634px;top:2664px">Contact Info</div>
<div class="abs f-small" style="left:634px;top:2694px">412 Harlow Lane</div>
<div class="abs f-small" style="left:634px;top:2717px">Brimsby, K07 31QT</div>
<svg class="abs" style="left:634px;top:2742px" width="12" height="12" viewBox="0 0 12 12"><path d="M2 1l2.5 0 1 3-1.5 1a7 7 0 0 0 3 3l1-1.5 3 1V11.5C6 11.5 .5 6 .5 2z" fill="#fff"/></svg>
<div class="abs f-small" style="left:667px;top:2740px">1-800-555-0142</div>
<svg class="abs" style="left:634px;top:2767px" width="13" height="10" viewBox="0 0 13 10"><rect width="13" height="10" fill="#fff"/><polyline points="0,0 6.5,5.5 13,0" fill="none" stroke="#1c4fd2" stroke-width="1.2"/></svg>
<div class="abs f-small" style="left:667px;top:2765px">hello@qzstreamhub.example</div>

<div class="abs f-head" style="left:885px;top:2664px">Email Sign Up</div>
<div class="abs email-box">Enter Email Address
  <svg width="13" height="10" viewBox="0 0 13 10"><rect width="13" height="10" fill="#222"/><polyline points="0,0 6.5,5.5 13,0" fill="none" stroke="#fff" stroke-width="1.2"/></svg>
</div>
<a class="btn" style="left:1037px;top:2754px;width:89px;height:34px;font-size:13px;font-weight:700">SIGN UP</a>

</body>
</html>
```